A website for a Maltese Law Firm

Our law firm needs a website to further its business. The site should have a simple yet effective design. We would need the following sections: About us, Practice Areas, About Malta, Contact. These should be further split as follows:

About us: Our firm, Our values, What others say, Offices

Practice Areas: Crimimal, Citizenship & Residence, Sovereign Patron Pathway, Criminal Defence, Civil Litigation, Arbitration and ADR, Commercial and Corporate, Media Law.

About Malta: just one section.

Contact: Just one section

We would also need a news feed at the front of the site to include latest news regarding our cases.

At the bottom we need a section for our Terms and a Privacy Statement.

Our logo is being attached.

Target Market(s)

All clients looking for legal assistance in Malta

Industry/Entity Type

Legal

Coding

Coded - Design and coding required

Number of Pages Required

1 page

Requirements
Must have
• It must be simple yet striking.

```html
<!DOCTYPE html>
<html lang="en">
<head>
<meta charset="utf-8">
<title>Borg &amp; Zammit Advocates</title>
<link href="https://fonts.googleapis.com/css2?family=Source+Sans+3:wght@400;600;700&family=Open+Sans:wght@400;600&display=swap" rel="stylesheet">
<style>
:root{
  --ink:#111;
  --dark:#1b1b1b;
  --band:#f7f7f7;
  --white:#fff;
  --muted:#555;
  --btn-top:#f2f2f2;
  --btn-bottom:#d4d4d4;
}
*{margin:0;padding:0;box-sizing:border-box}
html,body{width:686px;height:1200px;overflow:hidden;background:var(--white)}
body{font-family:"Open Sans",Arial,sans-serif;color:var(--ink);position:relative}
.heading{font-family:"Source Sans 3","Source Sans Pro",Arial,sans-serif;font-weight:700;text-transform:uppercase}
.btn{display:inline-flex;align-items:center;justify-content:center;font-family:"Source Sans 3",Arial,sans-serif;font-weight:700;font-size:8px;letter-spacing:.2px;color:var(--ink);background:linear-gradient(var(--btn-top),var(--btn-bottom));border-radius:2px;box-shadow:0 1px 2px rgba(0,0,0,.25)}

/* top bar */
.topbar{position:absolute;left:0;top:0;width:686px;height:27px;background:var(--dark);color:#ddd;font-size:6.5px}
.topbar .contact{position:absolute;left:76px;top:9px;display:flex;align-items:center;gap:5px}
.topbar .contact svg{width:7px;height:7px}
.topbar .sep{margin:0 4px}
.topbar .social{position:absolute;right:76px;top:11px;display:flex;gap:5px}
.topbar .social span{width:5px;height:5px;border-radius:50%;background:#ddd}

/* header */
.site-header{position:absolute;left:0;top:27px;width:686px;height:59px;background:var(--white)}
.brand{position:absolute;left:77px;top:21px;display:flex;align-items:center;gap:6px;font-family:"Source Sans 3",Arial,sans-serif;font-weight:600;font-size:12px;color:var(--ink)}
.brand-mark{width:9px;height:9px;background:var(--ink)}
.nav{position:absolute;right:76px;top:26px;display:flex;gap:27px;font-size:5.6px;color:#555}
.nav .active{color:var(--ink);font-weight:600}

/* hero */
.hero{position:absolute;left:0;top:86px;width:686px;height:230px;background:linear-gradient(90deg,#4d5a68 0%,#8a97a4 35%,#cfd7de 55%,#e9ecef 70%,#b9c2cb 100%)}
.hero-photo{position:absolute;left:340px;top:0;width:330px;height:230px;background:linear-gradient(180deg,#e9ecef 0%,#cfd4d9 60%,#3a3a3e 100%);opacity:.6}
.hero-copy{position:absolute;left:76px;top:62px;color:var(--white)}
.hero-copy h1{font-size:21px;text-shadow:0 1px 3px rgba(0,0,0,.5)}
.hero-copy p{margin-top:9px;font-size:6.4px;line-height:10px;width:240px}
.hero-copy .btn{margin-top:14px;width:68px;height:21px}
.dots{position:absolute;left:76px;top:178px;display:flex;gap:3px}
.dots span{width:4px;height:4px;border-radius:50%;background:var(--white)}
.dots span:first-child{background:none;border:1px solid var(--white)}

/* welcome */
.welcome{position:absolute;left:0;top:316px;width:686px;height:148px;text-align:center}
.welcome h2{margin-top:25px;font-size:18px}
.welcome p{margin:12px auto 0;width:540px;font-size:6.6px;line-height:11px;color:#222}
.welcome .btn{margin-top:13px;width:68px;height:22px}

/* practice areas */
.practice{position:absolute;left:0;top:464px;width:686px;height:366px;background:var(--band);box-shadow:inset 0 4px 6px -4px rgba(0,0,0,.15)}
.practice h2{position:absolute;top:32px;width:100%;text-align:center;font-size:18px}
.area{position:absolute;width:100px}
.area svg{width:28px;height:30px}
.area h3{margin-top:17px;font-size:10px;line-height:11px;letter-spacing:.2px}
.area p{margin-top:8px;font-size:6.2px;line-height:10.5px;color:#333}

/* news */
.news{position:absolute;left:0;top:830px;width:686px;height:254px;background:var(--white)}
.news h2{position:absolute;top:27px;width:100%;text-align:center;font-size:18px}
.arrows{position:absolute;left:322px;top:61px;display:flex;gap:6px}
.arrows span{width:17px;height:15px;border:1px solid var(--ink);display:flex;align-items:center;justify-content:center}
.card{position:absolute;top:101px;width:260px;height:112px;display:flex;background:var(--dark)}
.card .thumb{flex:0 0 107px;height:112px}
.card .body{flex:1;padding:18px 13px;color:var(--white)}
.card h3{font-size:10px}
.card time{display:block;margin-top:4px;font-size:5.8px}
.card p{margin-top:12px;font-size:6px;line-height:10.5px;color:#eee}

/* footer */
.site-footer{position:absolute;left:0;top:1084px;width:686px;height:116px;background:var(--dark);color:var(--white);text-align:center}
.site-footer h4{margin-top:21px;font-size:7px;font-weight:400;letter-spacing:.3px}
.site-footer p{margin:6px auto 0;width:540px;font-size:6.2px;line-height:11px}
.site-footer .social{margin-top:7px;display:flex;justify-content:center;gap:10px}
.site-footer .social span{width:8px;height:8px;border-radius:50%;background:var(--white)}
.site-footer small{display:block;margin-top:7px;font-size:5.2px}
</style>
</head>
<body>

<div class="topbar">
  <div class="contact">
    <svg viewBox="0 0 10 10"><path d="M2 1l2 2-1 1.5c.6 1.2 1.3 1.9 2.5 2.5L7 6l2 2-1.5 1.5C4.5 9 1 5.5.5 2.5z" fill="#ddd"/></svg>
    <span>(356) 2134 5870</span><span class="sep">|</span>
    <svg viewBox="0 0 10 10"><rect x=".5" y="2" width="9" height="6" fill="none" stroke="#ddd"/><path d="M.5 2l4.5 3.5L9.5 2" fill="none" stroke="#ddd"/></svg>
    <span>info@bzadvocates.com</span>
  </div>
  <div class="social"><span></span><span></span><span></span><span></span></div>
</div>

<header class="site-header">
  <div class="brand"><span class="brand-mark"></span>Borg &amp; Zammit Advocates</div>
  <nav class="nav"><span class="active">HOME</span><span>ABOUT US</span><span>PRACTICE AREAS</span><span>ABOUT MALTA</span><span>CONTACT US</span></nav>
</header>

<section class="hero" role="img" aria-label="Photo of a smiling lawyer in the foreground with colleagues blurred in an office behind">
  <div class="hero-photo"></div>
  <div class="hero-copy">
    <h1 class="heading">Law Firm From Malta</h1>
    <p>Lorem ipsum dolor sit amet, consectetur adipiscing elit proin quam urna, congue in magna sit amet.</p>
    <span class="btn">READ MORE</span>
  </div>
  <div class="dots"><span></span><span></span><span></span></div>
</section>

<section class="welcome">
  <h2 class="heading">Welcome to BZ Advocates</h2>
  <p>Lorem ipsum dolor sit amet, consectetur adipiscing elit, sed do eiusmod tempor incididunt ut labore et dolore magna aliqua. Ut enim ad minim veniam, quis nostrud exercitation ullamco laboris nisi ut aliquip ex ea commodo consequat. Duis aute irure dolor in reprehenderit in voluptate velit esse cillum dolore eu fugiat nulla pariatur.</p>
  <span class="btn">READ MORE</span>
</section>

<section class="practice">
  <h2 class="heading">Practice Areas</h2>

  <div class="area" style="left:76px;top:74px">
    <svg viewBox="0 0 28 30"><ellipse cx="14" cy="8" rx="12" ry="2.5"/><path d="M8 8V3h12v5z"/><circle cx="14" cy="12" r="5"/><rect x="9" y="10" width="10" height="2.5" fill="#fff"/><path d="M3 30c0-8 5-11 11-11s11 3 11 11z"/></svg>
    <h3 class="heading">Crimimal<br>Law</h3>
    <p>Lorem ipsum dolor sit amet, consectetur adipiscing elit, sed do eiusmod tempor</p>
  </div>
  <div class="area" style="left:222px;top:74px">
    <svg viewBox="0 0 28 30"><circle cx="14" cy="15" r="12" fill="none" stroke="#111" stroke-width="2"/><path d="M7 9c3 0 4 2 6 2s1 4 3 5-1 5-3 6c0-3-3-4-3-6s-4-2-3-7zM18 6c2 1 4 3 4 6-2 0-3-2-4-2z"/></svg>
    <h3 class="heading">Citizenship &amp;<br>Residence</h3>
    <p>Lorem ipsum dolor sit amet, consectetur adipiscing elit, sed do eiusmod tempor</p>
  </div>
  <div class="area" style="left:364px;top:74px">
    <svg viewBox="0 0 28 30"><ellipse cx="14" cy="9" rx="5.5" ry="7"/><path d="M2 30c0-8 5-11 12-11s12 3 12 11z"/><path d="M13 19h2l1 9h-4z" fill="#fff"/></svg>
    <h3 class="heading">Sovereign Patron<br>Pathway</h3>
    <p>Lorem ipsum dolor sit amet, consectetur adipiscing elit, sed do eiusmod tempor</p>
  </div>
  <div class="area" style="left:511px;top:74px">
    <svg viewBox="0 0 32 30"><circle cx="8" cy="20" r="6" fill="none" stroke="#111" stroke-width="2.2"/><circle cx="24" cy="14" r="6" fill="none" stroke="#111" stroke-width="2.2"/><path d="M8 14l3-8h4l3 7" fill="none" stroke="#111" stroke-width="1.5"/></svg>
    <h3 class="heading">Criminal<br>Defence</h3>
    <p>Lorem ipsum dolor sit amet, consectetur adipiscing elit, sed do eiusmod tempor</p>
  </div>

  <div class="area" style="left:76px;top:212px">
    <svg viewBox="0 0 28 30"><path d="M13 3h2v23h-2zM8 27h12v2H8zM3 7h22v1.5H3z"/><path d="M5 8L1 17h8zM23 8l-4 9h8z" fill="none" stroke="#111"/><path d="M1 17a4 3 0 0 0 8 0zM19 17a4 3 0 0 0 8 0z"/></svg>
    <h3 class="heading">Civil<br>Litigation</h3>
    <p>Lorem ipsum dolor sit amet, consectetur adipiscing elit, sed do eiusmod tempor</p>
  </div>
  <div class="area" style="left:222px;top:212px">
    <svg viewBox="0 0 28 30"><rect x="10" y="2" width="10" height="6" transform="rotate(35 15 5)"/><path d="M12 9l2.5 1.8L6 23l-2.5-1.8z"/><rect x="11" y="24" width="16" height="3"/><rect x="8" y="28" width="20" height="2"/></svg>
    <h3 class="heading">Arbitration and<br>&nbsp;ADR</h3>
    <p>Lorem ipsum dolor sit amet, consectetur adipiscing elit, sed do eiusmod tempor</p>
  </div>
  <div class="area" style="left:364px;top:212px">
    <svg viewBox="0 0 28 30"><path d="M14 2L1 8v3h26V8z"/><path d="M4 13h3v11H4zM9.5 13h3v11h-3zM15.5 13h3v11h-3zM21 13h3v11h-3zM2 25h24v2H2zM1 28h26v2H1z"/></svg>
    <h3 class="heading">Commercial&amp;<br>Corporate</h3>
    <p>Lorem ipsum dolor sit amet, consectetur adipiscing elit, sed do eiusmod tempor</p>
  </div>
  <div class="area" style="left:511px;top:212px">
    <svg viewBox="0 0 36 30"><path d="M13 4h10v4h-2V6h-6v2h-2z"/><rect x="1" y="8" width="34" height="20" rx="1.5"/><rect x="1" y="15" width="34" height="1.5" fill="#fff"/></svg>
    <h3 class="heading">Media<br>Law</h3>
    <p>Lorem ipsum dolor sit amet, consectetur adipiscing elit, sed do eiusmod tempor</p>
  </div>
</section>

<section class="news">
  <h2 class="heading">Latest News</h2>
  <div class="arrows">
    <span><svg width="6" height="8" viewBox="0 0 6 8"><path d="M5 0L1 4l4 4" fill="none" stroke="#111"/></svg></span>
    <span><svg width="6" height="8" viewBox="0 0 6 8"><path d="M1 0l4 4-4 4" fill="none" stroke="#111"/></svg></span>
  </div>
  <article class="card" style="left:76px">
    <div class="thumb" role="img" aria-label="Photo of hands typing on a laptop at a desk" style="background:linear-gradient(135deg,#c9a67e,#eee6dc 45%,#6d6f78)"></div>
    <div class="body">
      <h3 class="heading">Lorem Ipsum Dolor</h3>
      <time>Jun 08 ,2016</time>
      <p>Curabitur mollis neque vel ligula congue convallis id tristique Quisque ut nunc non mauris gravida dictum.\</p>
    </div>
  </article>
  <article class="card" style="left:350px">
    <div class="thumb" role="img" aria-label="Photo of a hand signing a document with a pen" style="background:linear-gradient(135deg,#5f7ea3,#dfe6ee 50%,#b58d6c)"></div>
    <div class="body">
      <h3 class="heading">Lorem Ipsum Dolor</h3>
      <time>Jun 08 ,2016</time>
      <p>Curabitur mollis neque vel ligula congue convallis id tristique Quisque ut nunc non mauris gravida dictum.\</p>
    </div>
  </article>
</section>

<footer class="site-footer">
  <h4>TERMS &amp; PRIVACY</h4>
  <p>Nemo enim ipsam voluptatem quia voluptas sit aspernatur aut odit aut fugit, sed quia consequuntur magni dolores eos qui ratione voluptatem sequi nesciunt. Neque porro quisquam est, qui dolorem ipsum quia dolor sit amet, consectetur, adipisci velit, sed quia non numquam</p>
  <div class="social"><span></span><span></span><span></span><span></span></div>
  <small>©2016 BZADVOCATES.COM. ALL RIGHT RESERVED.</small>
</footer>

</body>
</html>
```